I need 2 flyers designed for my business

Both can be similar in design and will have different purposes. I need an education based flyer and I need a government based flyer. The focus of the flyer will be software on the front and services on the back.
These all need to be 8.5x 11 in dimension (they can be full bleed). I would like to be able to print these out if needed. The design needs to look good with our website > www.brelmont.com

The software details are on the website.

```html
<!DOCTYPE html>
<html lang="en">
<head>
<meta charset="utf-8">
<title>Brelmont Flyers – Schools</title>
<link href="https://fonts.googleapis.com/css2?family=Poppins:wght@300;400;500;600;700&display=swap" rel="stylesheet">
<style>
:root{
  --bg:#a3a3a3;
  --red:#8a161b;
  --red-dark:#76121a;
  --olive:#85752f;
  --olive-light:#9a8a3d;
  --ink:#1f1f1f;
  --white:#ffffff;
}
*{box-sizing:border-box;margin:0;padding:0}
html,body{width:1200px;height:852px;overflow:hidden;background:var(--bg);font-family:"Poppins",sans-serif;color:var(--ink)}
.flyer{position:absolute;width:450px;height:583px;background:var(--white);overflow:hidden}
.flyer--software{left:115px;top:101px}
.flyer--services{left:592px;top:98px}

.hero-photo{position:absolute;left:0;top:0;width:450px;height:249px;
  background:
    linear-gradient(180deg,#dfe7ee 0%,#e9eef2 18%,#b9a48d 32%,#a65a43 48%,#9b513d 62%,#6e7a4a 76%,#4f7a33 88%,#7fa648 100%)}
.hero-photo--faded{background:
    linear-gradient(90deg,#fff 0%,rgba(255,255,255,.95) 28%,rgba(255,255,255,.55) 50%,rgba(255,255,255,0) 68%),
    linear-gradient(180deg,#dfe7ee 0%,#e9eef2 18%,#b9a48d 32%,#a65a43 48%,#9b513d 62%,#6e7a4a 76%,#4f7a33 88%,#7fa648 100%)}

.brand{position:absolute;display:flex;align-items:center;gap:6px;font-weight:700;font-size:11px;color:var(--red);letter-spacing:.3px}
.brand__mark{width:14px;height:14px;background:var(--red)}
.flyer--software .brand{left:17px;top:38px}
.flyer--services .brand{left:19px;top:38px}

.headline{position:absolute;left:17px;top:78px;font-size:19.5px;line-height:22px;text-transform:uppercase}
.headline__strong{display:block;font-weight:700;color:var(--red)}
.headline__light{display:block;font-weight:400;color:var(--olive)}
.intro{position:absolute;left:17px;top:195px;width:200px;font-size:6.3px;line-height:11.6px;font-weight:500}

.software-panel{position:absolute;left:0;top:249px;width:450px;height:208px}
.software-panel svg{position:absolute;left:0;top:0}
.module{position:absolute;width:34px;height:34px;margin:-17px 0 0 -17px;border-radius:50%;background:var(--olive);border:1px dashed #e8ddb0;display:flex;align-items:center;justify-content:center}
.module svg{width:16px;height:16px;stroke:#fff;fill:none;stroke-width:1.4}
.module-label{position:absolute;font-size:6.3px;line-height:7.8px;color:var(--white)}
.module-label--center{text-align:center;transform:translateX(-50%)}
.product-name{position:absolute;left:20px;top:88px;font-size:20px;font-weight:700;color:var(--red);letter-spacing:-.3px}

.benefits{position:absolute;left:287px;top:24px}
.section-title{font-size:15px;line-height:17px;text-transform:uppercase;white-space:nowrap}
.benefits .section-title{font-size:14px}
.section-title b{display:block;font-weight:700;color:var(--red)}
.section-title span{display:block;font-weight:400;color:var(--olive)}
.rule{display:flex;gap:2px;align-items:center;margin-top:5px;height:3px}
.rule i{display:block;height:2px;background:var(--olive)}
.rule i:first-child{width:20px}
.rule i:not(:first-child){width:2px;transform:skewX(-20deg)}
.rule--white i{background:var(--white)}

.check-list{list-style:none;margin-top:13px}
.check-list li{position:relative;padding-left:15px;font-size:7.2px;line-height:8.6px;margin-bottom:6.1px}
.benefits .check-list li{margin-bottom:5.4px}
.check-list li::before{content:"";position:absolute;left:0;top:.5px;width:7px;height:7px;border-radius:50%;background:var(--red)}
.check-list li::after{content:"";position:absolute;left:2.2px;top:1.6px;width:2.4px;height:3.8px;border:solid #fff;border-width:0 1.2px 1.2px 0;transform:rotate(40deg)}
.check-list--light li{color:var(--white)}
.check-list--light li::before{background:transparent}
.check-list--light li::after{border-color:#fff;left:2px;top:.6px;width:3px;height:5px}

.provides-band{position:absolute;left:0;top:457px;width:450px;height:71px;background:linear-gradient(90deg,var(--olive),var(--olive-light) 60%,var(--olive))}
.provides-title{position:absolute;left:26px;top:16px;color:var(--white);font-size:15px;line-height:17px;text-transform:uppercase}
.provides-title b{display:block;font-weight:600}
.provides-title span{display:block;font-weight:300}
.band-divider{position:absolute;top:12px;width:1px;height:46px;background:rgba(255,255,255,.35)}
.feature{position:absolute;top:17px;width:60px;margin-left:-30px;text-align:center;color:var(--white);font-size:7px;line-height:9px;font-weight:500}
.feature svg{display:block;margin:0 auto 4px;width:16px;height:16px;stroke:#fff;fill:none;stroke-width:1.4}

.contact-band{position:absolute;left:0;bottom:0;width:450px;height:54px;background:var(--red);color:var(--white)}
.contact-title{position:absolute;left:18px;top:8px;font-size:15px;line-height:17px}
.contact-title b{display:block;font-weight:700}
.contact-title span{display:block;font-weight:400}
.contact-title .rule{margin-top:3px}
.contact-divider{position:absolute;top:6px;width:1px;height:42px;background:rgba(255,255,255,.3)}
.contact-item{position:absolute;top:0;height:54px;display:flex;align-items:center;gap:6px}
.contact-item svg{width:11px;height:11px;stroke:#fff;fill:none;stroke-width:1.4;flex:none}
.contact-phone{font-size:11.5px}
.contact-web{font-size:7.5px}
.contact-address{font-size:6.5px;line-height:8px}

.service{position:absolute;left:0;width:450px}
.service--white{background:var(--white)}
.service--olive{background:var(--olive);color:var(--white)}
.service__icon{position:absolute;left:18px;width:24px;height:26px;stroke:var(--red);fill:none;stroke-width:1.3}
.service--olive .service__icon{stroke:#fff}
.service__title{position:absolute;left:18px;font-size:10.8px;line-height:12.5px;text-transform:uppercase;font-weight:600;color:var(--red)}
.service--olive .service__title{color:var(--white)}
.service__title .rule{margin-top:4px}
.service__text{position:absolute;left:146px;width:125px;font-size:7.3px;line-height:11.8px;font-weight:400}
.service__list{position:absolute;left:290px;width:150px}
.service__list h3{font-size:6.9px;font-weight:700;color:var(--red);text-transform:uppercase;margin-bottom:4px}
.service--olive .service__list h3{color:var(--white)}
.service__list .check-list{margin-top:0}
.service__list .check-list li{margin-bottom:5.6px;font-size:7.3px}
</style>
</head>
<body>

<section class="flyer flyer--software">
  <div class="hero-photo hero-photo--faded" role="img" aria-label="Photo of a red brick school building with a flag, trees and lawn"></div>
  <div class="brand"><span class="brand__mark"></span>CRESTLINE SOLUTIONS</div>
  <h1 class="headline">
    <span class="headline__strong">Comprehensive</span>
    <span class="headline__strong">Document</span>
    <span class="headline__light">Management</span>
    <span class="headline__light">Solution</span>
    <span class="headline__light">For Schools</span>
  </h1>
  <p class="intro">BRELMONT is actively operating in over 700 school districts in Ohio and in thousands of schools nationwide</p>

  <div class="software-panel">
    <svg width="450" height="208" viewBox="0 0 450 208">
      <polygon points="0,0 279,0 221,208 0,208" fill="#8a161b"/>
      <polygon points="279,0 287,0 229,208 221,208" fill="#85752f"/>
      <path d="M0,43 H70 A65.5 65.5 0 0 1 70,174 H0 Z" fill="#ffffff"/>
    </svg>

    <span class="module-label module-label--center" style="left:38px;top:7px">HR<br>Onboarding</span>
    <span class="module-label" style="left:111px;top:36px">eSigning</span>
    <span class="module-label" style="left:154px;top:69px">Scanning &amp; Database<br>Conversion</span>
    <span class="module-label" style="left:154px;top:126px">Mileage &amp; Expense<br>Tracking</span>
    <span class="module-label" style="left:111px;top:162px">Electronic Forms &amp;<br>Workflows</span>
    <span class="module-label module-label--center" style="left:38px;top:182px">Document<br>Archive</span>

    <div class="module" style="left:38px;top:45px"><svg viewBox="0 0 16 16"><circle cx="5" cy="5" r="2"/><circle cx="11" cy="5" r="2"/><path d="M2 13c0-3 6-3 6 0M8 13c0-3 6-3 6 0"/></svg></div>
    <div class="module" style="left:88px;top:45px"><svg viewBox="0 0 16 16"><rect x="2" y="5" width="10" height="8"/><path d="M5 11l7-8 2 2-7 8"/></svg></div>
    <div class="module" style="left:130px;top:79px"><svg viewBox="0 0 16 16"><rect x="4" y="2" width="8" height="12"/><path d="M6 6h4M6 9h4M2 8h12"/></svg></div>
    <div class="module" style="left:128px;top:133px"><svg viewBox="0 0 16 16"><path d="M2 12a6 6 0 0 1 12 0"/><path d="M8 12l3-4"/></svg></div>
    <div class="module" style="left:87px;top:163px"><svg viewBox="0 0 16 16"><rect x="3" y="2" width="9" height="12"/><path d="M5 5h5M5 8h5M5 11h3"/></svg></div>
    <div class="module" style="left:38px;top:161px"><svg viewBox="0 0 16 16"><rect x="3" y="8" width="10" height="6"/><path d="M5 8V3h6v5M7 11h2"/></svg></div>

    <div class="product-name">Brelmont</div>

    <div class="benefits">
      <h2 class="section-title"><b>Brelmont Software</b><span>Benefits</span></h2>
      <div class="rule"><i></i><i></i><i></i><i></i><i></i></div>
      <ul class="check-list">
        <li>Paperless HR System</li>
        <li>Applicant Tracking</li>
        <li>Contract/Salary Notice<br>Management</li>
        <li>Professional Development</li>
        <li>Mileage &amp; Expense Tracking</li>
        <li>Electronic Forms and Workflows</li>
        <li>Collect Digital Signatures</li>
        <li>Accept Credit Cards</li>
      </ul>
    </div>
  </div>

  <div class="provides-band">
    <div class="provides-title"><b>Brelmont</b><span>Provides</span><div class="rule rule--white"><i></i><i></i><i></i><i></i><i></i></div></div>
    <span class="band-divider" style="left:117px"></span>
    <div class="feature" style="left:155px"><svg viewBox="0 0 16 16"><rect x="2" y="4" width="12" height="10"/><path d="M2 8h12M7 10h2M4 2h8"/></svg>Unlimited<br>Storage</div>
    <div class="feature" style="left:216px"><svg viewBox="0 0 16 16"><circle cx="6" cy="8" r="4"/><path d="M10 5h4M10 8h4M10 11h4"/></svg>Web-Based<br>Access</div>
    <div class="feature" style="left:277px"><svg viewBox="0 0 16 16"><circle cx="8" cy="8" r="3"/><path d="M8 1v3M8 12v3M1 8h3M12 8h3M3 3l2 2M11 11l2 2M13 3l-2 2M3 13l2-2"/></svg>Disaster<br>Recovery</div>
    <div class="feature" style="left:338px"><svg viewBox="0 0 16 16"><rect x="4" y="7" width="8" height="7"/><path d="M6 7V4a2 2 0 0 1 4 0v3"/></svg>Document<br>Security</div>
    <div class="feature" style="left:399px"><svg viewBox="0 0 16 16"><path d="M2 6l6-3 6 3-6 3zM2 9l6 3 6-3M2 12l6 3 6-3"/></svg>Records<br>Retention</div>
  </div>

  <div class="contact-band">
    <div class="contact-title"><b>CONTACT</b><span>US</span><div class="rule rule--white"><i></i><i></i><i></i><i></i><i></i></div></div>
    <span class="contact-divider" style="left:97px"></span>
    <div class="contact-item contact-phone" style="left:108px"><svg viewBox="0 0 12 12"><path d="M3 1l2 2-1 2 3 3 2-1 2 2-2 2C5 11 1 7 1 3z"/></svg>(555) 014-2280</div>
    <span class="contact-divider" style="left:220px"></span>
    <div class="contact-item contact-web" style="left:230px"><svg viewBox="0 0 12 12"><circle cx="6" cy="6" r="5"/><path d="M1 6h10M6 1c3 3 3 7 0 10M6 1c-3 3-3 7 0 10"/></svg>www.brelmont.com</div>
    <span class="contact-divider" style="left:324px"></span>
    <div class="contact-item contact-address" style="left:340px"><svg viewBox="0 0 12 12" style="fill:#fff;stroke:none"><path d="M6 0a4 4 0 0 1 4 4c0 3-4 8-4 8S2 7 2 4a4 4 0 0 1 4-4z"/></svg><span>410 Meridian Parkway<br>Alder Falls, Ohio 44000</span></div>
  </div>
</section>

<section class="flyer flyer--services">
  <div class="hero-photo" role="img" aria-label="Photo of a red brick school building with a flag, trees and lawn"></div>
  <div class="brand"><span class="brand__mark"></span>CRESTLINE SOLUTIONS</div>

  <div class="service service--white" style="top:249px;height:87px">
    <svg class="service__icon" style="top:12px" viewBox="0 0 24 26"><path d="M1 5V1h4M19 1h4v4M1 21v4h4M19 25h4v-4"/><rect x="6" y="5" width="12" height="15"/><path d="M8 9h8M8 12h8M3 13h18"/></svg>
    <h2 class="service__title" style="top:49px">Document<br>Scanning Services<div class="rule"><i></i><i></i><i></i><i></i><i></i></div></h2>
    <p class="service__text" style="top:12px;width:128px">Fast, efficient process for the conversion of existing paper records to digital archives, increasing access and reducing onsite storage and costs.</p>
    <div class="service__list" style="top:13px">
      <h3>Scanning services for any format:</h3>
      <ul class="check-list">
        <li>Standard Office Documents</li>
        <li>16mm, 35mm Roll Microfilm</li>
        <li>Microfiche (Jackets or COM)</li>
        <li>Large Format Documents/Drawings</li>
      </ul>
    </div>
  </div>

  <div class="service service--olive" style="top:336px;height:100px">
    <svg class="service__icon" style="top:19px" viewBox="0 0 26 26"><rect x="1" y="3" width="15" height="18"/><path d="M4 1h14v16M4 8h9M4 11h9M4 14h6"/><circle cx="20" cy="20" r="3.5"/><path d="M20 15v1.5M20 23.5V25M15 20h1.5M23.5 20H25"/></svg>
    <h2 class="service__title" style="top:54px">Document<br>Storage Services<div class="rule rule--white"><i></i><i></i><i></i><i></i><i></i></div></h2>
    <p class="service__text" style="top:15px;width:120px">Solution for offsite document storage and retrieval to effectively store, manage, and safeguard your vital business records and documents.</p>
    <div class="service__list" style="top:16px">
      <h3>A local, convenient solution:</h3>
      <ul class="check-list check-list--light">
        <li>Free Up Office Space</li>
        <li>Reduce Costs</li>
        <li>Keep Records in a Fireproof,<br>Waterproof &amp; Wind-Safe Facility</li>
      </ul>
    </div>
  </div>

  <div class="service service--white" style="top:436px;height:93px">
    <svg class="service__icon" style="top:13px" viewBox="0 0 24 26"><rect x="6" y="1" width="12" height="10"/><path d="M8 4h8M8 7h8"/><rect x="2" y="11" width="20" height="6"/><path d="M5 17v8M9 17v8M13 17v8M17 17v8"/></svg>
    <h2 class="service__title" style="top:45px">Secure Document<br>Shredding<div class="rule"><i></i><i></i><i></i><i></i><i></i></div></h2>
    <p class="service__text" style="left:142px;top:12px;width:112px">Safely and cost-effectively destroy unnecessary paper-based documents. One-time or recurring, our solutions are tailored to you.</p>
    <div class="service__list" style="left:286px;top:10px;width:160px">
      <h3>Destroy unnecessary documents:</h3>
      <ul class="check-list">
        <li>Protect confidential information</li>
        <li>Reduce the cost of managing<br>information that is no longer useful</li>
        <li>Ensure compliance with regulations<br>for information destruction</li>
      </ul>
    </div>
  </div>

  <div class="contact-band">
    <div class="contact-title"><b>CONTACT</b><span>US</span><div class="rule rule--white"><i></i><i></i><i></i><i></i><i></i></div></div>
    <span class="contact-divider" style="left:97px"></span>
    <div class="contact-item contact-phone" style="left:108px"><svg viewBox="0 0 12 12"><path d="M3 1l2 2-1 2 3 3 2-1 2 2-2 2C5 11 1 7 1 3z"/></svg>(555) 014-2280</div>
    <span class="contact-divider" style="left:220px"></span>
    <div class="contact-item contact-web" style="left:230px"><svg viewBox="0 0 12 12"><circle cx="6" cy="6" r="5"/><path d="M1 6h10M6 1c3 3 3 7 0 10M6 1c-3 3-3 7 0 10"/></svg>www.brelmont.com</div>
    <span class="contact-divider" style="left:324px"></span>
    <div class="contact-item contact-address" style="left:340px"><svg viewBox="0 0 12 12" style="fill:#fff;stroke:none"><path d="M6 0a4 4 0 0 1 4 4c0 3-4 8-4 8S2 7 2 4a4 4 0 0 1 4-4z"/></svg><span>410 Meridian Parkway<br>Alder Falls, Ohio 44000</span></div>
  </div>
</section>

</body>
</html>
```